Larkspur Talent IT Recruiting firm needs a business card design for Recruiters, Sourcers, and Account

We need business cards that allow us to change all contact info, names, titles (Recruiter, Sourcer, Account Manager, Director, CEO, etc) per person since we have three offices, in three cities, Phoenix, Austin, and Las Vegas. We do recruiting and contractors for IT positions (Developers, Architects, Software Engineers, Security Engineers, Help Desk, DBAs, PMs, Scrum Masters, etc.) Our client companies are very diverse from Meridian 100 to silicone Valley type start-ups.

So, while we what hip, techie, and quirky, it still needs to be professional. Primary color we use is blue, with silver as a secondary color.

Target Market(s)

IT, Technology

Industry/Entity Type

Business

Contact Information for Business Card

Company name: Larkspur Talent, Inc.
Website: www.larkspurtalent.example
Logos for Careerloop, Blipster, and Myriada

Name, Title, Office Number, Cell Number, email

Font styles to use
Serif
Sans Serif

Colors
0455a3
d5d5d5

Requirements
Nice to have
• The grey I selected below is not necessary - but, would like silver included. I included a card design (File 3: LTI early trial example.jpg) that I had started on. It's very rough, and not quite what we're looking for, but what we did like is the logo, big, maybe a bit faded, off center, goes out of frame, etc. Still looking for other ideas - you are the pros! But, just an idea of a design element we liked.

```html
<!DOCTYPE html>
<html lang="en">
<head>
<meta charset="utf-8">
<title>Larkspur Talent — Business Cards</title>
<link rel="stylesheet" href="https://fonts.googleapis.com/css2?family=Marcellus&family=Lato:wght@400;700&display=swap">
<style>
  :root {
    --page: #eceef1;
    --brand-blue: #0455a3;
    --sky-top: #45b6f2;
    --sky-bottom: #0b62d8;
    --accent-blue: #2f9df0;
    --silver: #d5d5d5;
    --card-white: #ffffff;
    --card-fade: #eef0f2;
    --ink: #1e1e1e;
    --ink-soft: #333333;
    --white: #ffffff;
    --serif: "Marcellus", "Times New Roman", serif;
    --sans: "Lato", "Helvetica Neue", Arial, sans-serif;
  }
  * { box-sizing: border-box; margin: 0; padding: 0; }
  html, body { width: 1200px; height: 900px; overflow: hidden; }
  body { background: var(--page); position: relative; font-family: var(--sans); }

  .card {
    position: absolute;
    width: 560px;
    height: 320px;
    border-radius: 4px;
    overflow: hidden;
    box-shadow: 0 14px 30px rgba(0,0,0,.18), 0 2px 6px rgba(0,0,0,.12);
  }

  /* Back card */
  .card--back {
    left: 70px; top: 110px;
    background: linear-gradient(180deg, var(--sky-top) 0%, var(--sky-bottom) 100%);
    color: var(--white);
  }
  .card--back .emblem-fade {
    position: absolute; right: -120px; top: -40px;
    width: 340px; height: 340px; border-radius: 50%;
    background: radial-gradient(circle at 40% 40%, rgba(255,255,255,.22), rgba(255,255,255,.04) 70%);
  }
  .card--back .brand {
    position: absolute; left: 60px; top: 92px;
    font-family: var(--serif); font-size: 34px; letter-spacing: 4px;
    color: var(--white); white-space: nowrap;
  }
  .card--back .tagline {
    position: absolute; left: 96px; top: 150px;
    font-family: var(--sans); font-size: 12px; letter-spacing: 2.4px;
    text-transform: uppercase;
  }
  .card--back .website {
    position: absolute; left: 190px; top: 190px;
    font-size: 15px; letter-spacing: .3px;
  }
  .card--back .social {
    position: absolute; left: 230px; top: 222px;
    display: flex; gap: 12px; font-size: 10px; letter-spacing: .4px;
  }
  .social span { display: flex; align-items: center; gap: 4px; }
  .social i {
    display: inline-block; width: 9px; height: 9px; border-radius: 50%;
    background: var(--white);
  }

  /* Front card */
  .card--front {
    left: 570px; top: 470px;
    background: linear-gradient(135deg, var(--card-white) 0%, var(--card-fade) 100%);
    color: var(--ink);
  }
  .card--front .watermark {
    position: absolute; left: 60px; top: 10px;
    width: 300px; height: 300px; border-radius: 50%;
    background: radial-gradient(circle, rgba(213,213,213,.35), rgba(213,213,213,0) 70%);
  }
  .card--front .emblem {
    position: absolute; right: -70px; top: -30px;
    width: 230px; height: 300px;
    border-radius: 0 0 0 100%;
    background: linear-gradient(160deg, #58bdf5 0%, var(--accent-blue) 45%, #1570e0 100%);
  }
  .card--front .brand {
    position: absolute; left: 38px; top: 72px;
    font-family: var(--serif); font-size: 32px; letter-spacing: 3.5px;
    color: var(--ink); white-space: nowrap;
  }
  .card--front .tagline {
    position: absolute; left: 58px; top: 128px;
    font-family: var(--sans); font-size: 11.5px; letter-spacing: 2.2px;
    text-transform: uppercase; color: var(--ink-soft);
  }
  .card--front .person {
    position: absolute; right: 200px; top: 158px; text-align: right;
  }
  .person .name { font-weight: 700; font-size: 18px; }
  .person .title { font-size: 13px; color: var(--accent-blue); margin-top: 1px; }
  .card--front .contact {
    position: absolute; right: 200px; top: 215px;
    list-style: none; text-align: right; font-size: 15px; line-height: 21px;
  }
  .contact li { display: flex; justify-content: flex-end; align-items: center; gap: 5px; }
  .contact svg { width: 11px; height: 11px; fill: var(--accent-blue); }
</style>
</head>
<body>

  <section class="card card--back">
    <div class="emblem-fade" role="img" aria-label="Large faded brand emblem running off the card edge"></div>
    <div class="brand">LARKSPUR TALENT</div>
    <p class="tagline">Tech hiring, done right</p>
    <p class="website">www.larkspurtalent.example</p>
    <div class="social">
      <span><i></i>Myriada</span>
      <span><i></i>Blipster</span>
      <span><i></i>Careerloop</span>
    </div>
  </section>

  <section class="card card--front">
    <div class="watermark" role="img" aria-label="Faint silver brand emblem watermark"></div>
    <div class="emblem" role="img" aria-label="Large blue brand emblem cropped by the card edge"></div>
    <div class="brand">LARKSPUR TALENT</div>
    <p class="tagline">Tech hiring, done right</p>
    <div class="person">
      <p class="name">Avery Lin</p>
      <p class="title">Designation</p>
    </div>
    <ul class="contact">
      <li>555 014-2288
        <svg viewBox="0 0 12 12" aria-hidden="true"><path d="M1 4c0-2 2-3 5-3s5 1 5 3l-2 1-1-1H4L3 5z"/><rect x="2.5" y="6" width="7" height="5" rx="1"/></svg>
      </li>
      <li>555 014-2288
        <svg viewBox="0 0 12 12" aria-hidden="true"><path d="M3.5 0.5h5a1 1 0 0 1 1 1v9a1 1 0 0 1-1 1h-5a1 1 0 0 1-1-1v-9a1 1 0 0 1 1-1zm0.6 1.5v7h3.8V2z"/></svg>
      </li>
      <li>info@larkspurtalent.example
        <svg viewBox="0 0 12 12" aria-hidden="true"><path d="M0.5 2.5h11v7h-11zM1.5 3.3l4.5 3.4 4.5-3.4z" fill-rule="evenodd"/></svg>
      </li>
    </ul>
  </section>

</body>
</html>
```